Agrarhandel benötigt Homepage
Zielgruppe
Wir sind ein Agrarhandel mit einem Warenumschlagslager im Sinne eines klassischen Einzelhandels und vertreiben Produkte an Landwirte.
Wir vertreiben folgende Hauptproduktgruppen:
Einzelfuttermittel
wie z.B. Sojaexktraktionsschrot. Die einzelnen Produkte könnten z.B. wie die Futtermittel auf folgender Seite dargestellt werden (https://www.kornprobe-beispiel.eu/de/produkt/trelomixan)
Mischfuttermittel
Hier bieten wir unseren Kunden an, individuelles Mischfutter auf Basis unserer Einzelfuttermittel herzustellen.
Weitere Details und weitere Produktbereiche habe ich in einer Powerpoint-Übersicht dargestellt.
Neben diesen Produkten wollen wir uns als Familienunternehmen selbst vorstellen. Zudem betreiben wir in unserer Familie zusätzlich einen Milchviehbetrieb den wir ebenfalls hervorheben möchten, da wir unseren Kunden gegenüber einerseits als Zulieferer aber auch als Kollege auftreten wollen.
Einzelfuttermittel: Hier können wir durch unsere Unabhängigkeit punkten, da wir nicht abhängig von bestimmten Lieferanten sind und dementsprechend unabhängig beraten können. Wir untersuchen im Vergleich zu unseren Wettbewerben die Qualität der Futtermittel bis ins Detail und können daher eine Transparenz bieten, die Konkurrenten in der Regel nicht bieten können. Unser Warenumschlagsplatz mit moderner Technik ermöglicht es uns äußerst kosteneffizient die Waren umschlagen und ausliefern zu können.
Mischfuttermittel: Auf Basis der vorhandenen Einzelfuttermittel stellen wir je nach Kundenwunsch individuelle Mischfutter her. Wir arbeiten mit offenen Deklarationen, sodass unsere Kunden jederzeit nachvollziehen können, ob auch die Einzelfuttermittel verwendet wurden, die sie bestellt haben und keine billigen Ersatzprodukte verwendet wurden.
Zudem sind wir BT und HUPA zertifiziert. Die aktuellen für unser Unternehmen ausgestellten Zertifikate müssen für unsere Kunden als Download zur Verfügung stehen. Statt dem HUPA-Logo bitte das ..
Aufgabenstellung
Wir möchten gerne ein zeitgemäße Homepage, jedoch muss auch berücksichtigt werden, dass unsere Kunden eher konservativ denken.

```html
<!DOCTYPE html>
<html lang="de">
<head>
<meta charset="utf-8">
<title>Futterkonfigurator – Feldhof Agrar</title>
<link rel="stylesheet" href="https://fonts.googleapis.com/css2?family=Manrope:wght@400;500&family=Arimo:wght@400;500&display=swap">
<style>
:root{
  --green:#1d6a50;
  --orange:#f9a620;
  --panel:#f1f1f1;
  --track:#cfcfcf;
  --ink:#3a3a3a;
  --dark:#3a2418;
  --page:#ffffff;
}
*{box-sizing:border-box;margin:0;padding:0}
html,body{width:674px;height:1200px;overflow:hidden;background:var(--page)}
body{position:relative;font-family:"Manrope",sans-serif;color:var(--ink)}
.screen{position:absolute;left:89px;width:502px;height:331px;overflow:hidden}
.screen--1{top:59px}.screen--2{top:423px}.screen--3{top:787px}
.hero-photo{position:absolute;inset:0;
  background:radial-gradient(ellipse at 15% 60%,#7a4a2c 0%,#4a2a18 35%,transparent 60%),
  radial-gradient(ellipse at 50% 110%,#8a7660 0%,#4d3a2b 30%,transparent 55%),
  linear-gradient(180deg,#1d120c 0%,#2f1c12 50%,#3d2a1e 100%)}
.brand{position:absolute;left:32px;top:27px;display:flex;align-items:center;gap:4px;
  font-family:"Manrope",sans-serif;font-weight:500;font-size:8px;color:#fff}
.brand-dot{width:8px;height:8px;border-radius:50%;background:#fff}
.nav{position:absolute;top:27px;left:224px;display:flex;align-items:center;height:11px;
  font-family:"Arimo",sans-serif;font-size:4.6px;color:#fff;letter-spacing:.05px}
.nav span{margin-right:10.5px}
.nav .caret{font-size:3.5px;margin-left:1px}
.shop-btn{position:absolute;left:405px;top:27px;width:45px;height:11px;background:var(--orange);
  color:#fff;font-family:"Arimo",sans-serif;font-size:4.6px;display:flex;align-items:center;justify-content:center}
.panel{position:absolute;left:51px;top:72px;width:400px;height:224px;background:var(--panel)}
.step-title{position:absolute;left:17px;top:16px;color:var(--green);font-size:13.5px;line-height:13px;font-weight:400}
.progress{position:absolute;left:17px;top:45px;width:175px;height:4px;background:var(--track)}
.progress i{display:block;height:100%;background:var(--orange)}
.intro{position:absolute;left:0;right:0;top:77px;text-align:center;font-size:5.4px;line-height:7px}
.col{position:absolute;top:94px}
.col h3{font-size:8.3px;font-weight:400;margin-bottom:6px;color:#3a2418}
.opt{display:flex;align-items:center;gap:2.5px;font-size:5.4px;height:14px}
.box{width:4.5px;height:4.5px;border:.6px solid #444;background:#fff;position:relative}
.box svg{position:absolute;left:-.4px;top:-.6px}
.opt.is-checked span{border-bottom:.6px solid var(--orange);line-height:6px}
.btn{position:absolute;top:194px;height:14px;display:flex;align-items:center;justify-content:center;font-size:6px}
.btn--next{background:var(--orange);color:#fff;width:40px}
.btn--back{border:.8px solid #333;color:#333;width:43px;left:146px}
.side{position:absolute;right:0;width:22px;height:22px;background:#3a2418;display:flex;align-items:center;justify-content:center}
.scroll-hint{position:absolute;left:245px;top:313px}
.slider{position:absolute;left:112px;top:96.5px;width:175px;height:3px;background:var(--track)}
.slider i{display:block;width:88px;height:100%;background:var(--green)}
.knob{position:absolute;left:84px;top:-3px;width:9px;height:9px;border-radius:50%;background:var(--orange)}
.qty{position:absolute;left:178px;top:112px;width:43px;height:14px;border:.8px solid #999;background:#f6f6f6;
  font-size:5.6px;display:flex;align-items:center;justify-content:center}
</style>
</head>
<body>

<!-- ========== Step 1 ========== -->
<section class="screen screen--1">
  <div class="hero-photo" role="img" aria-label="Nahaufnahme eines braun-weißen Rindes im Stall, gedämpftes Licht"></div>
  <div class="brand"><span class="brand-dot"></span>Feldhof Agrar</div>
  <nav class="nav"><span>ÜBER UNS</span><span>PRODUKTE<b class="caret">⌄</b></span><span>PARTNER</span><span>DOWNLOADS</span><span>KONTAKT</span></nav>
  <div class="shop-btn">ONLINESHOP</div>
  <div class="panel">
    <h2 class="step-title">Schritt 1:<br>Tierarten auswählen</h2>
    <div class="progress"><i style="width:20%"></i></div>
    <p class="intro">Entscheiden Sie, für welche Tierarten das Futter geeignet sein soll:</p>
    <div class="col" style="left:93px"><h3>Milchkühe</h3>
      <div class="opt is-checked"><b class="box"><svg width="5" height="5" viewBox="0 0 10 10"><path d="M2 5l2 2 4-5" stroke="#222" stroke-width="1.6" fill="none"/></svg></b><span>Milchkühe</span></div>
      <div class="opt is-checked"><b class="box"><svg width="5" height="5" viewBox="0 0 10 10"><path d="M2 5l2 2 4-5" stroke="#222" stroke-width="1.6" fill="none"/></svg></b><span>Kuhkälber</span></div>
    </div>
    <div class="col" style="left:146px"><h3>Rindermast</h3>
      <div class="opt is-checked"><b class="box"><svg width="5" height="5" viewBox="0 0 10 10"><path d="M2 5l2 2 4-5" stroke="#222" stroke-width="1.6" fill="none"/></svg></b><span>Mastkälber</span></div>
      <div class="opt is-checked"><b class="box"><svg width="5" height="5" viewBox="0 0 10 10"><path d="M2 5l2 2 4-5" stroke="#222" stroke-width="1.6" fill="none"/></svg></b><span>Mastrinder</span></div>
      <div class="opt"><b class="box"></b><span>Fresser</span></div>
    </div>
    <div class="col" style="left:212px"><h3>Schwein</h3>
      <div class="opt"><b class="box"></b><span>Sauen</span></div>
      <div class="opt"><b class="box"></b><span>Mast</span></div>
      <div class="opt"><b class="box"></b><span>Färkel</span></div>
    </div>
    <div class="col" style="left:267px"><h3>Geflügel</h3>
      <div class="opt"><b class="box"></b><span>Legehenen</span></div>
      <div class="opt"><b class="box"></b><span>Masthühner</span></div>
    </div>
    <div class="btn btn--next" style="left:180px">WEITER</div>
  </div>
  <div class="side" style="top:258px"><svg width="11" height="8" viewBox="0 0 22 16"><rect x="1" y="1" width="20" height="14" fill="none" stroke="#fff" stroke-width="1.6"/><path d="M1 1l10 8 10-8M1 15l7-6M21 15l-7-6" stroke="#fff" stroke-width="1.4" fill="none"/></svg></div>
  <div class="side" style="top:283px"><svg width="7" height="11" viewBox="0 0 14 22"><rect x="1" y="1" width="12" height="20" rx="2" fill="none" stroke="#fff" stroke-width="1.6"/><circle cx="7" cy="18" r="1" fill="#fff"/></svg></div>
  <div class="side" style="top:309px"><svg width="11" height="11" viewBox="0 0 22 22"><path d="M11 2a9 9 0 0 0-7.7 13.6L2 20l4.5-1.2A9 9 0 1 0 11 2z" fill="none" stroke="#fff" stroke-width="1.6"/><path d="M8 7c0 4 3 7 7 7l1-2-2-1-1 1c-1-.5-2.5-2-3-3l1-1-1-2z" fill="#fff"/></svg></div>
  <svg class="scroll-hint" width="12" height="18" viewBox="0 0 12 18"><rect x="1" y="1" width="10" height="16" rx="5" fill="none" stroke="#fff" stroke-width="1"/><path d="M6 3v7M3.5 7.5L6 10l2.5-2.5" stroke="#fff" stroke-width="1" fill="none"/></svg>
</section>

<!-- ========== Step 2 ========== -->
<section class="screen screen--2">
  <div class="hero-photo" role="img" aria-label="Nahaufnahme eines braun-weißen Rindes im Stall, gedämpftes Licht"></div>
  <div class="brand"><span class="brand-dot"></span>Feldhof Agrar</div>
  <nav class="nav"><span>ÜBER UNS</span><span>PRODUKTE<b class="caret">⌄</b></span><span>PARTNER</span><span>DOWNLOADS</span><span>KONTAKT</span></nav>
  <div class="shop-btn">ONLINESHOP</div>
  <div class="panel">
    <h2 class="step-title">Schritt 2:<br>Futtersorten festlegen</h2>
    <div class="progress"><i style="width:40%"></i></div>
    <p class="intro">Entscheiden Sie, welche Komponenten im Futter enthalten sein sollen:</p>
    <div class="col" style="left:92px;top:93px">
      <div class="opt"><b class="box"></b><span>Europäischer Sojaschrot</span></div>
      <div class="opt"><b class="box"></b><span>Rapsschrot/-kuchen</span></div>
      <div class="opt"><b class="box"></b><span>Geschützter Rapsschrot</span></div>
    </div>
    <div class="col" style="left:184px;top:93px">
      <div class="opt"><b class="box"></b><span>Leinschrot</span></div>
      <div class="opt"><b class="box"></b><span>Maiskleberfutter</span></div>
      <div class="opt"><b class="box"></b><span>Körnermais</span></div>
    </div>
    <div class="col" style="left:256px;top:93px">
      <div class="opt"><b class="box"></b><span>Melasseschnitzel</span></div>
      <div class="opt"><b class="box"></b><span>Weizenkleie</span></div>
      <div class="opt"><b class="box"></b><span>Hamstoff</span></div>
    </div>
    <div class="btn btn--back">ZURÜCK</div>
    <div class="btn btn--next" style="left:211px">WEITER</div>
  </div>
  <div class="side" style="top:258px"><svg width="11" height="8" viewBox="0 0 22 16"><rect x="1" y="1" width="20" height="14" fill="none" stroke="#fff" stroke-width="1.6"/><path d="M1 1l10 8 10-8M1 15l7-6M21 15l-7-6" stroke="#fff" stroke-width="1.4" fill="none"/></svg></div>
  <div class="side" style="top:283px"><svg width="7" height="11" viewBox="0 0 14 22"><rect x="1" y="1" width="12" height="20" rx="2" fill="none" stroke="#fff" stroke-width="1.6"/><circle cx="7" cy="18" r="1" fill="#fff"/></svg></div>
  <div class="side" style="top:309px"><svg width="11" height="11" viewBox="0 0 22 22"><path d="M11 2a9 9 0 0 0-7.7 13.6L2 20l4.5-1.2A9 9 0 1 0 11 2z" fill="none" stroke="#fff" stroke-width="1.6"/><path d="M8 7c0 4 3 7 7 7l1-2-2-1-1 1c-1-.5-2.5-2-3-3l1-1-1-2z" fill="#fff"/></svg></div>
  <svg class="scroll-hint" width="12" height="18" viewBox="0 0 12 18"><rect x="1" y="1" width="10" height="16" rx="5" fill="none" stroke="#fff" stroke-width="1"/><path d="M6 3v7M3.5 7.5L6 10l2.5-2.5" stroke="#fff" stroke-width="1" fill="none"/></svg>
</section>

<!-- ========== Step 3 ========== -->
<section class="screen screen--3">
  <div class="hero-photo" role="img" aria-label="Nahaufnahme eines braun-weißen Rindes im Stall, gedämpftes Licht"></div>
  <div class="brand"><span class="brand-dot"></span>Feldhof Agrar</div>
  <nav class="nav"><span>ÜBER UNS</span><span>PRODUKTE<b class="caret">⌄</b></span><span>PARTNER</span><span>DOWNLOADS</span><span>KONTAKT</span></nav>
  <div class="shop-btn">ONLINESHOP</div>
  <div class="panel">
    <h2 class="step-title">Schritt 3:<br>Menge in Kilogramm</h2>
    <div class="progress"><i style="width:60%"></i></div>
    <p class="intro">Geben Sie die gewünschte Menge in Kilogramm an, um die exakte<br>Zusammensetzung des Futters zu bestimmen.</p>
    <div class="slider"><i></i><b class="knob"></b></div>
    <div class="qty">2500 KG</div>
    <div class="btn btn--back">ZURÜCK</div>
    <div class="btn btn--next" style="left:211px">WEITER</div>
  </div>
  <div class="side" style="top:258px"><svg width="11" height="8" viewBox="0 0 22 16"><rect x="1" y="1" width="20" height="14" fill="none" stroke="#fff" stroke-width="1.6"/><path d="M1 1l10 8 10-8M1 15l7-6M21 15l-7-6" stroke="#fff" stroke-width="1.4" fill="none"/></svg></div>
  <div class="side" style="top:283px"><svg width="7" height="11" viewBox="0 0 14 22"><rect x="1" y="1" width="12" height="20" rx="2" fill="none" stroke="#fff" stroke-width="1.6"/><circle cx="7" cy="18" r="1" fill="#fff"/></svg></div>
  <div class="side" style="top:309px"><svg width="11" height="11" viewBox="0 0 22 22"><path d="M11 2a9 9 0 0 0-7.7 13.6L2 20l4.5-1.2A9 9 0 1 0 11 2z" fill="none" stroke="#fff" stroke-width="1.6"/><path d="M8 7c0 4 3 7 7 7l1-2-2-1-1 1c-1-.5-2.5-2-3-3l1-1-1-2z" fill="#fff"/></svg></div>
  <svg class="scroll-hint" width="12" height="18" viewBox="0 0 12 18"><rect x="1" y="1" width="10" height="16" rx="5" fill="none" stroke="#fff" stroke-width="1"/><path d="M6 3v7M3.5 7.5L6 10l2.5-2.5" stroke="#fff" stroke-width="1" fill="none"/></svg>
</section>

</body>
</html>
```